Lotus Market Hall VIP Card(Magnetic strip plastic card)

We need Fancy,Simple,VIP customer card design for a grocery store name"Lotus Market Hall", Chinese name"福润商场“.Major color should be Dark red. This design is based on a VIP gift card project, which means design should consider about the back side with magnetic strip area and mostly it will be plastic material.

Target Market(s)

Rich Customers

Industry/Entity Type

Grocery Store

Contact Information for Business Card

People actually put more than $1000 into the card for shopping

Font styles to use
Serif
Sans Serif
Decorative
Script
Other font styles liked:
• Fancy

Colors
ec1f27
fbed22

Requirements
Must have
• Red color
Nice to have
• Better logo transformation.

```html
<!DOCTYPE html>
<html lang="en">
<head>
<meta charset="utf-8">
<title>Lotus Market Hall VIP Card</title>
<link rel="stylesheet" href="https://fonts.googleapis.com/css2?family=Arimo:wght@400;700&family=Noto+Serif+SC:wght@400&display=swap">
<style>
  :root {
    --card-black: #000000;
    --brand-yellow: #fbed22;
    --stripe-yellow: #fdf000;
    --brand-red: #ec1f27;
    --fine-print: #b3a800;
    --ink: #111111;
    --page: #ffffff;
  }
  * { margin: 0; padding: 0; box-sizing: border-box; }
  html, body {
    width: 1200px; height: 1200px; overflow: hidden;
    background: var(--page);
    font-family: "Arimo", Arial, sans-serif;
  }
  .canvas { position: relative; width: 1200px; height: 1200px; }

  .card {
    position: absolute;
    width: 585px; height: 365px;
    border-radius: 18px;
    overflow: hidden;
    transform-origin: top left;
  }
  .card--small { transform: scale(0.8); }

  /* Front */
  .card-front { background: var(--card-black); }
  .dragon-art {
    position: absolute; left: 0; top: 0; width: 200px; height: 365px;
    background: linear-gradient(90deg, rgba(251,237,34,0.85) 0%, rgba(251,237,34,0.45) 55%, rgba(251,237,34,0) 100%);
  }
  .brand-name {
    position: absolute; left: 0; width: 100%; padding-left: 200px; padding-right: 30px;
    top: 112px; text-align: center;
    color: var(--brand-red); font-weight: 700; font-size: 26px; letter-spacing: 0.5px;
  }
  .brand-name-cn {
    position: absolute; left: 0; width: 100%; padding-left: 200px; padding-right: 30px;
    top: 193px; text-align: center;
    color: var(--brand-yellow); font-family: "Noto Serif SC", serif; font-size: 33px;
  }
  .tier {
    position: absolute; left: 0; width: 100%; padding-left: 200px; padding-right: 30px;
    top: 258px; text-align: center;
    color: var(--brand-yellow); font-weight: 700; font-size: 28px; letter-spacing: 1px;
  }
  .tagline {
    position: absolute; left: 136px; top: 332px;
    color: var(--brand-red); font-size: 9.5px; white-space: nowrap;
  }

  /* Back */
  .card-back { background: var(--stripe-yellow); }
  .card-back--raised { box-shadow: 0 22px 40px rgba(0,0,0,0.28), 0 4px 10px rgba(0,0,0,0.12); }
  .mag-stripe {
    position: absolute; left: 0; top: 38px; width: 100%; height: 61px;
    background: var(--card-black);
  }
  .holder-name {
    position: absolute; left: 0; width: 100%; top: 163px; text-align: center;
    color: var(--ink); font-size: 32px; letter-spacing: 1.5px;
  }
  .terms {
    position: absolute; left: 21px; top: 244px; width: 549px;
    color: var(--fine-print); font-size: 13px; line-height: 16px; text-align: justify;
  }
</style>
</head>
<body>
<div class="canvas">

  <div class="card card-back card-back--raised" style="left:512px; top:345px;">
    <div class="mag-stripe"></div>
    <div class="holder-name">MAYA LINDEN</div>
    <p class="terms">This "Card" contains value which may be used to purchase goods with the exception of other Cards. Please present it to a sales associate at the time of purchase and amounts will be deducted from the Card balance. This Card may not be redeemed for cash and the unused value remains on the Card. Merchant is not responsible for lost, stolen or damaged Cards or any unauthorized use.</p>
  </div>

  <div class="card card-front" style="left:94px; top:115px;">
    <div class="dragon-art" role="img" aria-label="Yellow line illustration of a coiling dragon"></div>
    <div class="brand-name">Lotus Market Hall</div>
    <div class="brand-name-cn">福润商场</div>
    <div class="tier">V.I.P.</div>
    <div class="tagline">People actually put more than $1000 into the card for shopping</div>
  </div>

  <div class="card card--small card-front" style="left:94px; top:830px;">
    <div class="dragon-art" role="img" aria-label="Yellow line illustration of a coiling dragon"></div>
    <div class="brand-name">Lotus Market Hall</div>
    <div class="brand-name-cn">福润商场</div>
    <div class="tier">V.I.P.</div>
    <div class="tagline">People actually put more than $1000 into the card for shopping</div>
  </div>

  <div class="card card--small card-back" style="left:628px; top:830px;">
    <div class="mag-stripe"></div>
    <div class="holder-name">MAYA LINDEN</div>
    <p class="terms">This "Card" contains value which may be used to purchase goods with the exception of other Cards. Please present it to a sales associate at the time of purchase and amounts will be deducted from the Card balance. This Card may not be redeemed for cash and the unused value remains on the Card. Merchant is not responsible for lost, stolen or damaged Cards or any unauthorized use.</p>
  </div>

</div>
</body>
</html>
```